Loom Harbor needs a website

I sell rugs and carpet on my website, loomharborfloors.example. I need help with the site design to make it "pop". The logo in the header has been designed and I want the site to match it's style and color. Also I have some example sites for layout:
matsquick.example
weave-outlet.example

Industry/Entity Type

Carpet

Requirements
Must have
• Scrolling images on front page. I will insert photos, just need the code.

```html
<!DOCTYPE html>
<html lang="en">
<head>
<meta charset="utf-8">
<title>Loom Harbor – Rugs &amp; Carpet Flooring</title>
<link rel="stylesheet" href="https://fonts.googleapis.com/css2?family=Open+Sans:wght@400;600;700&display=swap">
<style>
:root{
  --green:#6aab3c;
  --green-dark:#4f8f27;
  --green-light:#86c255;
  --navy:#1f3e6b;
  --navy-deep:#173056;
  --hero-blue:#2d5a92;
  --price:#5d9e2e;
  --text:#4a4a4a;
  --muted:#666;
  --line:#e2e2e2;
  --panel:#f6f6f6;
  --footer:#f3f3f3;
  --white:#fff;
}
*{box-sizing:border-box;margin:0;padding:0}
html,body{width:814px;height:1200px;overflow:hidden}
body{position:relative;background:var(--white);font-family:"Open Sans",Arial,sans-serif;color:var(--text);font-size:9px}
a{color:inherit;text-decoration:none}
ul{list-style:none}

.header-band{position:absolute;left:0;top:0;width:814px;height:114px;background:linear-gradient(#fff 70%,#f2f2f2)}
.account-links{position:absolute;right:76px;top:11px;font-size:8.5px;color:var(--navy)}
.account-links span{color:#999;margin:0 5px}
.brand{position:absolute;left:75px;top:34px;display:flex;align-items:center;gap:8px}
.brand-mark{width:26px;height:26px;border-radius:50%;background:var(--navy)}
.brand-name{font-size:22px;font-weight:600;color:var(--navy);letter-spacing:.5px}
.search{position:absolute;left:274px;top:50px;width:259px;height:34px;background:#e9e9e9;border-radius:2px;padding:5px}
.search-field{width:100%;height:24px;background:var(--white);border:1px solid #ddd;font-size:8px;color:#777;padding:6px 8px;position:relative}
.search-btn{position:absolute;right:0;top:-1px;width:26px;height:24px;background:var(--navy);display:flex;align-items:center;justify-content:center}
.call{position:absolute;right:76px;top:46px;text-align:right}
.call-label{font-size:11px;color:var(--green)}
.call-number{font-size:16px;color:var(--navy);display:flex;align-items:center;gap:3px;margin-top:1px}

.main-nav{position:absolute;left:69px;top:94px;width:676px;height:39px;background:linear-gradient(var(--green-light),var(--green-dark));display:flex;color:var(--white);font-size:11.5px}
.main-nav a{display:flex;align-items:center;padding:0 15px;border-right:1px solid rgba(255,255,255,.35)}
.main-nav .home{width:49px;justify-content:center;padding:0}
.main-nav .cart{margin-left:auto;border-right:0;border-left:1px solid rgba(255,255,255,.35);font-size:9px;gap:5px;padding:0 9px}

.hero{position:absolute;left:69px;top:141px;width:673px;height:272px;overflow:hidden}
.hero-photo{position:absolute;inset:0;background:linear-gradient(120deg,#b3201c 0%,#1e2d6b 28%,#c12a22 45%,#d8b48a 62%,#e2c29a 100%)}
.hero-panel{position:absolute;inset:0}
.hero-copy{position:absolute;left:466px;top:68px;color:var(--white);width:190px}
.hero-kicker{font-size:17px;color:#d9e4f2}
.hero-title{font-size:25px;margin-top:1px}
.hero-text{font-size:8px;line-height:13px;margin-top:9px;color:#e6edf6}
.hero-dots{display:flex;gap:3px;margin-top:11px}
.hero-dots i{width:9px;height:9px;border-radius:50%;background:var(--white)}

.sidebox{position:absolute;left:69px;width:155px;border:1px solid var(--line);background:var(--white)}
.sidebox h3{font-size:12px;font-weight:400;color:var(--navy);padding:10px 19px 6px;border-bottom:1px solid var(--line);background:var(--panel)}
.sidebox ul{padding:10px 0 8px 23px}
.sidebox li{font-size:8.5px;color:var(--muted);line-height:20.5px;position:relative;padding-left:9px}
.sidebox li::before{content:"";position:absolute;left:0;top:8px;border-left:3px solid #555;border-top:2.5px solid transparent;border-bottom:2.5px solid transparent}

.section-title{position:absolute;font-size:14px;font-weight:400}
.featured-title{left:242px;top:442px;color:var(--navy)}
.latest-title{left:240px;top:805px;color:var(--green)}

.product-grid{position:absolute;left:239px;top:468px;display:grid;grid-template-columns:repeat(4,124px);grid-auto-rows:153px;column-gap:4px;row-gap:8px}
.product-card{border:1px solid var(--line);background:var(--white)}
.product-img{height:83px}
.product-name{font-size:10px;color:#444;margin:9px 0 0 11px}
.product-price{font-size:9px;color:var(--price);margin:1px 0 0 11px}
.product-price s{color:var(--price)}
.add-btn{display:inline-block;margin:7px 0 0 10px;background:var(--navy);color:var(--white);font-size:7px;font-weight:700;padding:5px 9px;border-radius:2px}

.style-strip{position:absolute;left:239px;top:832px;width:509px;height:112px;display:flex;gap:1px}
.style-tile{flex:1;position:relative}
.style-tile::after{content:"";position:absolute;left:0;right:0;bottom:0;height:25px;background:rgba(40,30,25,.45)}

.site-footer{position:absolute;left:0;top:975px;width:814px;height:185px;background:var(--footer);border-top:1px solid var(--line)}
.footer-col{position:absolute;top:25px}
.footer-col h4{font-size:14px;font-weight:400;color:var(--green);margin-bottom:6px}
.footer-col li{font-size:8.5px;color:var(--muted);line-height:18px}
.socials{display:flex;gap:6px;margin-top:6px}
.socials i{width:15px;height:15px;border-radius:2px;display:block}
.footer-brand{display:flex;align-items:center;gap:6px;margin:18px 0 0 -7px}
.footer-brand .brand-mark{width:20px;height:20px}
.footer-brand .brand-name{font-size:17px}
.legal{position:absolute;left:89px;top:1176px;font-size:8.5px;color:#777}
</style>
</head>
<body>

<div class="header-band"></div>
<nav class="account-links"><a href="#">My Account</a><span>|</span><a href="#">Sign In</a><span>|</span><a href="#">Cart $0.00</a><span>|</span><a href="#">Checkout</a></nav>

<a class="brand" href="#"><span class="brand-mark"></span><span class="brand-name">Loom Harbor</span></a>

<form class="search"><div class="search-field">Type flooring here
  <span class="search-btn"><svg width="13" height="13" viewBox="0 0 13 13"><circle cx="5.5" cy="5.5" r="4" fill="none" stroke="#fff" stroke-width="1.6"/><line x1="8.5" y1="8.5" x2="12" y2="12" stroke="#fff" stroke-width="1.8"/></svg></span>
</div></form>

<div class="call">
  <div class="call-label">Call Us Now</div>
  <div class="call-number"><svg width="14" height="14" viewBox="0 0 24 24"><path d="M6.6 10.8a15 15 0 0 0 6.6 6.6l2.2-2.2c.3-.3.7-.4 1-.2 1.1.4 2.3.6 3.6.6.6 0 1 .4 1 1V20c0 .6-.4 1-1 1A17 17 0 0 1 3 4c0-.6.4-1 1-1h3.5c.6 0 1 .4 1 1 0 1.3.2 2.5.6 3.6.1.3 0 .7-.2 1z" fill="var(--navy)"/></svg>555.014.2287</div>
</div>

<nav class="main-nav">
  <a class="home" href="#" aria-label="Home"><svg width="17" height="15" viewBox="0 0 17 15"><path d="M8.5 0 0 7.5h2.5V15h4.5v-5h3v5h4.5V7.5H17z" fill="#fff"/></svg></a>
  <a href="#">About Us</a><a href="#">Carpet Flooring</a><a href="#">Specials</a><a href="#">Order Now</a><a href="#">Support</a><a href="#">Contact</a>
  <a class="cart" href="#"><svg width="20" height="18" viewBox="0 0 20 18"><path d="M0 1h3l3 10h11l2-7H5" fill="none" stroke="#fff" stroke-width="1.5"/><circle cx="8" cy="15" r="1.6" fill="#fff"/><circle cx="15" cy="15" r="1.6" fill="#fff"/></svg>My Cart: 0 item</a>
</nav>

<section class="hero">
  <div class="hero-photo" role="img" aria-label="Red and navy patterned area rug lying on a light wooden floor"></div>
  <svg class="hero-panel" width="673" height="272" viewBox="0 0 673 272">
    <defs><radialGradient id="panelGlow" cx="0.5" cy="0.35" r="0.8"><stop offset="0" stop-color="#3d6ca6"/><stop offset="1" stop-color="#1f4478"/></radialGradient></defs>
    <path d="M460 0Q392 136 475 272H673V0Z" fill="url(#panelGlow)"/>
  </svg>
  <div class="hero-copy">
    <div class="hero-kicker">Special Designs</div>
    <div class="hero-title">Cartpet Flooring</div>
    <p class="hero-text">Etiam est nunc venenatis in tristique eu imperdiet ac nisl Cum sociis natoque penatibus et magnis dis parturient montes</p>
    <div class="hero-dots"><i></i><i></i><i></i><i></i></div>
  </div>
</section>

<aside class="sidebox" style="top:436px;height:222px">
  <h3>Shop by Category</h3>
  <ul><li>Commercial Flooring</li><li>Carpet Flooring</li><li>Harwood Flooring</li><li>Area Rugs</li><li>Mauris vel lacus</li><li>Vitae felis vestibulum</li><li>Etiam est nunc</li><li>Tristique imperdiet</li></ul>
</aside>
<aside class="sidebox" style="top:666px;height:136px">
  <h3>Show by Colors</h3>
  <ul><li>Blacks &amp; Greys</li><li>Blues</li><li>Browns</li><li>Burgundys</li></ul>
</aside>
<aside class="sidebox" style="top:808px;height:137px">
  <h3>Brands &amp; Material</h3>
  <ul><li>Acrylic</li><li>Bamboo</li><li>Chenille</li><li>Cotton</li></ul>
</aside>

<h2 class="section-title featured-title">FEATURED PRODUCTS</h2>
<div class="product-grid">
  <article class="product-card"><div class="product-img" role="img" aria-label="Brown textured carpet sample" style="background:linear-gradient(135deg,#8a5a4c,#6e4438)"></div><h5 class="product-name">Product Name</h5><p class="product-price">Price: <s>$11.69</s> – $9.39</p><a class="add-btn" href="#">ADD TO CART</a></article>
  <article class="product-card"><div class="product-img" role="img" aria-label="Beige and dark brown diamond patterned carpet" style="background:linear-gradient(135deg,#b39a74,#4e3a28)"></div><h5 class="product-name">Product Name</h5><p class="product-price">Price: <s>$11.69</s> – $9.39</p><a class="add-btn" href="#">ADD TO CART</a></article>
  <article class="product-card"><div class="product-img" role="img" aria-label="Orange medallion patterned rug" style="background:radial-gradient(circle,#f0b260,#c3591c)"></div><h5 class="product-name">Product Name</h5><p class="product-price">Price: <s>$11.69</s> – $9.39</p><a class="add-btn" href="#">ADD TO CART</a></article>
  <article class="product-card"><div class="product-img" role="img" aria-label="Brown and cream geometric patterned rug" style="background:linear-gradient(135deg,#6a3e2c,#c7ab8c)"></div><h5 class="product-name">Product Name</h5><p class="product-price">Price: <s>$11.69</s> – $9.39</p><a class="add-btn" href="#">ADD TO CART</a></article>
  <article class="product-card"><div class="product-img" role="img" aria-label="Tan and brown traditional medallion rug" style="background:radial-gradient(circle,#c9a679,#6f4b2e)"></div><h5 class="product-name">Product Name</h5><p class="product-price">Price: <s>$11.69</s> – $9.39</p><a class="add-btn" href="#">ADD TO CART</a></article>
  <article class="product-card"><div class="product-img" role="img" aria-label="Red and orange ornamental rug" style="background:linear-gradient(135deg,#c84a2a,#e07a45)"></div><h5 class="product-name">Product Name</h5><p class="product-price">Price: <s>$11.69</s> – $9.39</p><a class="add-btn" href="#">ADD TO CART</a></article>
  <article class="product-card"><div class="product-img" role="img" aria-label="Rolled shag rugs in cream, brown and red" style="background:linear-gradient(180deg,#d8d0c8,#8a6b5a 60%,#b2392c)"></div><h5 class="product-name">Product Name</h5><p class="product-price">Price: <s>$11.69</s> – $9.39</p><a class="add-btn" href="#">ADD TO CART</a></article>
  <article class="product-card"><div class="product-img" role="img" aria-label="Soft beige floral patterned carpet" style="background:linear-gradient(135deg,#c9b497,#a88e6e)"></div><h5 class="product-name">Product Name</h5><p class="product-price">Price: <s>$11.69</s> – $9.39</p><a class="add-btn" href="#">ADD TO CART</a></article>
</div>

<h2 class="section-title latest-title">LATEST STYLES &amp; DESIGNS</h2>
<div class="style-strip">
  <div class="style-tile" role="img" aria-label="Fan of multicoloured carpet samples" style="background:linear-gradient(120deg,#b44a2f,#d69a6a,#8a6a52)"></div>
  <div class="style-tile" role="img" aria-label="Light beige plush carpet on a wooden floor" style="background:linear-gradient(160deg,#cbbfae,#a89884)"></div>
  <div class="style-tile" role="img" aria-label="Colourful carpet tile squares" style="background:linear-gradient(135deg,#b6452c,#d2a54a,#7a8a3a)"></div>
  <div class="style-tile" role="img" aria-label="Close-up of peach coloured carpet texture" style="background:linear-gradient(135deg,#ebc6a4,#d9ae88)"></div>
</div>

<footer class="site-footer">
  <div class="footer-col" style="left:87px"><h4>Information</h4><ul><li>About Us</li><li>Latest Products</li><li>Order Now</li><li>Best Sellings</li><li>Testimonials</li></ul></div>
  <div class="footer-col" style="left:204px"><h4>Products</h4><ul><li>Suspendisse</li><li>Vulputate aliquam</li><li>Dui Nulla elementum</li><li>Dui ut augue</li><li>Aliquam vehicula</li></ul></div>
  <div class="footer-col" style="left:337px"><h4>Sublinks</h4><ul><li>Suspendisse</li><li>Vulputate aliquam</li><li>Dui Nulla elementum</li><li>Dui ut augue</li><li>Aliquam vehicula</li></ul></div>
  <div class="footer-col" style="left:463px"><h4>Support</h4><ul><li>Support</li><li>FAQ</li><li>Return &amp; Order</li><li>My Account</li><li>Contact Us</li></ul></div>
  <div class="footer-col" style="left:582px"><h4>Get in touch</h4><ul><li>Please connect with us on followings</li></ul>
    <div class="socials"><i style="background:#3b5998"></i><i style="background:#4fb3e8"></i><i style="background:#1a78b0"></i><i style="background:#f08a24"></i></div>
    <div class="footer-brand"><span class="brand-mark"></span><span class="brand-name">Loom Harbor</span></div>
  </div>
</footer>
<p class="legal">© 2014 Company Name &nbsp;All right reserved &nbsp;Term of Use</p>

</body>
</html>
```